Occasions chocolate packaging

We are looking for 7 packaging designs for bars of chocolate.

Each design needs to be different and we’re not looking for a consistent brand or branding message across the designs. Inspiration should come from gift/occasion cards. Fun, simple, bold, vibrant colours and eye catching, i.e. not vintage or just text.

The front of the packaging should have the main message on and is free of any branding. You don’t need to design the back, just simply allow the main background colour or design pattern to continue around.

These are the different designs we are after, I’ve added in some text for each to give you some guidance but feel free to play around with the message if it suits the design better.

1) Mum
‘The best mum’, ‘Best mum in the World’, ‘Number 1 Mum’

2) Dad
‘The Best Dad’, ‘Best Dad Ever’, ‘Number 1 Dad’, ‘You’re my hero Dad’

3) Husband
‘Best Husband in the World’, ‘Husband I Love You’, ‘Darling Husband’

4) Wife
‘Best Wife in the World’, ‘For my Wonderful Wife’, ‘My Beautiful Wife’

5) Congratulations
Simple one, just Congratulations

6) Thinking of you
Try and keep this neutral as it could be used for happy and sad situations.

7) Thank you
Keep this gender neutral.

Sides:
The sides need to have the following text:

FINE BELGIAN DARK CHOCOLATE
infused with Orange

Back:
The main colour of the front should continue all the way around, we will place a box with the contents and bar code on here ourselves so no need to do anything.

Dimensions:
Attached in the document, front of package is 85mm by 190mm.

The packaging is made from folded card, the first blank part is for gluing the back on to.

Reason: I'm extending the deadline as I've only received 1 design so far which has followed the brief. Although I do like it, I would like to see at least some competition...

```html
<!DOCTYPE html>
<html lang="en">
<head>
<meta charset="utf-8">
<title>Best Husband in the World – Chocolate Bar Wrapper</title>
<link rel="stylesheet" href="https://fonts.googleapis.com/css2?family=Cormorant+Garamond:wght@400&family=Lato:wght@300&family=Parisienne&display=swap">
<style>
  :root {
    --wrapper-yellow: #ffff66;
    --fold-line: #f4f45c;
    --kiss-pink: #e5006a;
  }
  html, body {
    margin: 0;
    padding: 0;
    overflow: hidden;
    background: var(--wrapper-yellow);
  }
  .wrapper {
    position: relative;
    width: 1200px;
    height: 2170px;
    background: var(--wrapper-yellow);
    overflow: hidden;
  }
  .artwork {
    position: absolute;
    top: 0;
    left: 0;
    width: 1200px;
    height: 2170px;
  }
  .product-name {
    font-family: "Cormorant Garamond", serif;
    font-weight: 400;
    font-size: 145px;
    fill: var(--kiss-pink);
  }
  .flavour {
    font-family: "Lato", sans-serif;
    font-weight: 300;
    font-size: 82px;
    fill: var(--kiss-pink);
  }
  .greeting {
    font-family: "Parisienne", cursive;
    font-weight: 400;
    font-size: 150px;
    fill: var(--kiss-pink);
  }
  .fold-line {
    fill: var(--fold-line);
  }
  .kiss-artwork {
    fill: var(--kiss-pink);
  }
</style>
</head>
<body>
  <main class="wrapper">
    <svg class="artwork" viewBox="0 0 1200 2170">
      <rect class="fold-line" x="1084" y="0" width="3" height="2170"/>

      <text class="product-name" transform="translate(108 2148) rotate(-90)" textLength="2135" lengthAdjust="spacingAndGlyphs">FINE BELGIAN DARK CHOCOLATE</text>
      <text class="flavour" transform="translate(1178 1443) rotate(-90)" textLength="700" lengthAdjust="spacingAndGlyphs">infused with orange</text>

      <ellipse class="kiss-artwork" cx="602" cy="770" rx="483" ry="255" role="img" aria-label="Bold pink lipstick kiss mark"/>

      <g role="heading" aria-level="1">
        <text class="greeting line-one" transform="translate(130 1595) rotate(-25.7)" textLength="950" lengthAdjust="spacingAndGlyphs">Best Husband</text>
        <text class="greeting line-two" transform="translate(239 1780) rotate(-25.7)" textLength="880" lengthAdjust="spacingAndGlyphs">in the World</text>
      </g>
    </svg>
  </main>
</body>
</html>
```